Road Construction Company needs business cards

We would like a new business card designed for our business.

We're a road construction company based in Qld, Australia.

Can the business card please have the following information on it.

Name: Warren Halbeck
Position: General Manager
Phone: 0472 915 348
Email: Warren.halbeck@tovrin.com.au
Address: 87 Marrow Ave, Pendlebay, QLD, 4023
Website: www.tovrin.com.au

Visually we'd like the card to be professional and simple.

Attached is our logo.

Our website is www.tovrin.com.au

Target Market(s)

Men aged 25-60

Contact Information for Business Card

As listed in project description

Font styles to use
Serif

Requirements
Must have
• Large logo on back of card

```html
<!DOCTYPE html>
<html lang="en">
<head>
<meta charset="utf-8">
<title>Tovrin Business Card</title>
<link href="https://fonts.googleapis.com/css2?family=Inter:wght@400;700;800&display=swap" rel="stylesheet">
<style>
  :root {
    --stage: #9a9a9a;
    --brand-blue: #0b4f9f;
    --brand-deep: #1a3a84;
    --brand-light: #3a7cc6;
    --accent: #2f8fd9;
    --ink: #0d4a9d;
    --text: #4a4a4a;
    --card-white: #ffffff;
  }
  * { margin: 0; padding: 0; box-sizing: border-box; }
  html, body {
    width: 1200px; height: 588px; overflow: hidden;
    background: var(--stage);
    font-family: "Inter", Arial, sans-serif;
  }
  .canvas { position: relative; width: 1200px; height: 588px; }

  .card {
    position: absolute;
    width: 486px; height: 287px;
    top: 142px;
  }

  /* Front */
  .card-front { left: 87px; overflow: hidden; }
  .card-front .pattern-fill {
    position: absolute; inset: 0;
    background: linear-gradient(100deg, var(--brand-deep) 0%, var(--brand-blue) 45%, var(--brand-light) 100%);
  }
  .brand {
    position: absolute; left: 0; right: 0; top: 98px;
    text-align: center;
    color: var(--card-white);
    font-weight: 800;
    font-size: 60px;
    letter-spacing: 2px;
    line-height: 1;
  }

  /* Back */
  .card-back { left: 622px; background: var(--card-white); }
  .identity {
    position: absolute; right: 279px; top: 118px;
    text-align: right;
  }
  .identity .name {
    color: var(--ink);
    font-weight: 700;
    font-size: 20px;
    letter-spacing: 0.2px;
    line-height: 1.1;
    white-space: nowrap;
  }
  .identity .role {
    margin-top: 3px;
    color: var(--text);
    font-size: 13.5px;
  }
  .divider {
    position: absolute; left: 229px; top: 117px;
    width: 1.5px; height: 50px;
    background: var(--ink);
  }
  .contacts {
    position: absolute; left: 247px; top: 113px;
    list-style: none;
  }
  .contacts li {
    display: flex; align-items: center;
    height: 18.5px;
    color: var(--text);
    font-size: 13.5px;
    white-space: nowrap;
  }
  .contacts svg { width: 11px; height: 11px; margin-right: 4px; fill: var(--accent); }
  .address {
    position: absolute; left: 0; right: 0; top: 250px;
    text-align: center;
    color: var(--text);
    font-size: 13.5px;
  }
</style>
</head>
<body>
<main class="canvas">
  <section class="card card-front">
    <div class="pattern-fill" role="img" aria-label="Repeating pattern of the brand symbol in shades of blue"></div>
    <div class="brand">TOVRIN</div>
  </section>

  <section class="card card-back">
    <div class="identity">
      <div class="name">WARREN HALBECK</div>
      <div class="role">General Manager</div>
    </div>
    <div class="divider"></div>
    <ul class="contacts">
      <li>
        <svg viewBox="0 0 24 24" aria-hidden="true"><path d="M6.6 10.8a15 15 0 0 0 6.6 6.6l2.2-2.2a1 1 0 0 1 1-.25 11.4 11.4 0 0 0 3.6.57 1 1 0 0 1 1 1V20a1 1 0 0 1-1 1A17 17 0 0 1 3 4a1 1 0 0 1 1-1h3.5a1 1 0 0 1 1 1c0 1.25.2 2.45.57 3.6a1 1 0 0 1-.25 1z"/></svg>
        0472 915 348
      </li>
      <li>
        <svg viewBox="0 0 24 24" aria-hidden="true"><path d="M2 5h20v2l-10 6L2 7z"/><path d="M2 9l10 6 10-6v10H2z"/></svg>
        Warren.halbeck@tovrin.com.au
      </li>
      <li>
        <svg viewBox="0 0 24 24" aria-hidden="true"><circle cx="12" cy="12" r="10"/></svg>
        www.tovrin.com.au
      </li>
    </ul>
    <div class="address">87 Marrow Ave, Pendlebay, QLD, 4023</div>
  </section>
</main>
</body>
</html>
```